Web Design Project

Brightfold Publishing owns and operates a large number of editorial websites. These websites provides mostly consumers in the financial services space with information and price comparisons for a particular service.

Brightfold Publishing, as the holding company for each of these sites, currently has no website. We need to build a website targeted towards potential partners for our websites. The idea being that when we start a conversation with a partner, they can view our site and obtain some basic information about who we are.

The structure of the site is to be very simple, containing only a brief description about who we are, our contact details and a list of some of our websites:
• CoverVault.net.au
• MotorPolicyCheck.com.au
• DwellingCoverCheck.com.au
• MedicalCoverCheck.com.au
• LegacyCoverCheck.com.au
• JourneyCoverCheck.com.au
• AnimalCoverCheck.com.au
• PrivateLendingCheck.com.au
• MobileCoolingUnit.com.au
• FixedSavingsYield.com.au
• ThriftyHousehold.com.au
• CoinNana.com.au
• TameYourPlastic.com.au
• PurseMinder.com.au
• ThirdPartyClaimsCoverNational.com.au
• Trade-Cover.com.au
• MotorPolicyProviders.com.au
• MedicalCoverProviders.com.au
• DwellingCoverHub.com
• LegacyCoverHub.com
• EarningsShieldCoverHub.com
• MedicalCoverHub.com
• AnimalCoverHub.com
• PrivateLendingHub.com
• ChargePlasticHub.com
• DwellingLendingHub.com
• RetireNestEgg.net.au

The design of the site should say 'Internet company', 'professional', 'fresh thinking'. The design should not look like a corporate site that you would see from any corporate services business with images of people in suits. We are ultimately an Internet business and there should be a unique feel to the site.

We are open to a suggestion of a colour pallet as the holding company does not have an established logo.

Some sites that we like are:

http://www.quillmarsh-studio.co.uk/#home
http://previewbox00.layoutdock.example/wt_52418/index.html
http://previewbox00.layoutdock.example/wordpress_61942/
http://ponderloop.example/
http://www.brindlux.example/
http://www.tobiasvrankel.example/
http://www.slickfrontdoors.example/Corporate/design-ideas-detail.html?id=4197
http://pairmint.example/
http://orvendal.example/

Reason: Hi all, Apologies, but I need to extend the timeline. One of our key stakeholders is away for the next week. There are a few good designs that we have received to date and there are some tweaks that we would like to see before making a final decision. Thank you to everyone that has submitted designs - Have a great new year. Derek

Reason: Sorry to have to delay the deadline on this, but we did not find anything in the designs really resonated with us. We will have a further think about the existing designs that have been submitted and how we can provide more specific feedback to the designers to make some modifications to the designs.

Target Market(s)

We are targeting insurance companies / brokers that we are talking to. The idea is that we show a professional face to them.

Industry/Entity Type

Financial

Requirements
Must have
• Home Page (possibly integrated with About us details)
Contact Us
Our Sites

```html
<!DOCTYPE html>
<html lang="en">
<head>
<meta charset="utf-8">
<title>Contact Us – Brightfold Publishing</title>
<link rel="stylesheet" href="https://fonts.googleapis.com/css2?family=Anton&family=Noto+Sans:wght@400;700&family=Arimo&display=swap">
<style>
  :root {
    --top-band: #033a6c;
    --sky-top: #0b8bf4;
    --sky-bottom: #cfe7fc;
    --logo-panel: #0b365d;
    --logo-gold: #f2a90c;
    --nav-idle: #b7dcfd;
    --nav-active: #ffffff;
    --heading-blue: #0b8bf4;
    --text-dark: #333333;
    --panel-grey: #f3f3f3;
    --field-border: #cccccc;
    --accent-orange: #f7943c;
    --button-top: #2eaee4;
    --button-bottom: #0b76bf;
    --footer-top: #033a6c;
    --footer-bottom: #000000;
    --snow: #eef6fd;
    --ice: #8fc8e8;
  }
  * { box-sizing: border-box; margin: 0; padding: 0; }
  html, body { width: 1200px; height: 949px; overflow: hidden; background: #ffffff; }
  .page { position: relative; width: 1200px; height: 949px; font-family: "Noto Sans", Verdana, sans-serif; color: var(--text-dark); }

  .masthead { position: absolute; left: 0; top: 0; width: 1200px; height: 250px;
    background: linear-gradient(180deg, var(--sky-top) 0%, var(--sky-top) 20%, var(--sky-bottom) 100%); overflow: hidden; }
  .masthead__band { position: absolute; left: 0; top: 0; width: 100%; height: 18px; background: var(--top-band); }
  .brand { position: absolute; left: 35px; top: 0; height: 84px; padding: 24px 14px 0 18px; background: var(--logo-panel); }
  .brand__name { font-family: "Anton", Impact, sans-serif; font-size: 37px; line-height: 1; color: var(--logo-gold); letter-spacing: 0.5px; white-space: nowrap; }
  .main-nav { position: absolute; left: 52px; top: 87px; display: flex; gap: 0; font-family: "Arimo", Arial, sans-serif; font-size: 17.5px; }
  .main-nav a { text-decoration: none; color: var(--nav-idle); }
  .main-nav a.is-current { color: var(--nav-active); }
  .main-nav .nav-home { width: 87px; }
  .main-nav .nav-sites { width: 116px; }
  .page-title { position: absolute; left: 51px; top: 192px; font-family: "Anton", Impact, sans-serif; font-size: 60px; line-height: 1; color: var(--heading-blue); letter-spacing: 0.5px; }
  .peak-art { position: absolute; left: 731px; top: 106px; width: 264px; height: 144px;
    background: radial-gradient(ellipse at 50% 100%, var(--snow) 0%, var(--snow) 45%, var(--ice) 70%, rgba(207,231,252,0) 72%); }

  .section-heading { position: absolute; font-size: 23px; font-weight: 400; line-height: 1; color: var(--text-dark); }
  .details-heading { left: 51px; top: 299px; }
  .message-heading { left: 600px; top: 299px; }

  .details-card { position: absolute; left: 37px; top: 339px; width: 378px; height: 161px; background: var(--panel-grey); padding: 20px 15px; font-size: 18px; line-height: 22px; }
  .details-card__company { color: var(--accent-orange); font-weight: 700; font-size: 18.5px; }
  .details-card__line--gap { margin-top: 4px; }
  .details-card__line--gap2 { margin-top: 5px; }

  .contact-form label { position: absolute; left: 599px; font-size: 14px; line-height: 1; color: var(--text-dark); }
  .contact-form .field { position: absolute; left: 600px; background: var(--panel-grey); border: 1px solid var(--field-border); font: inherit; }
  .label-name { top: 340px; } .field-name { top: 357px; width: 347px; height: 32px; }
  .label-email { top: 411px; } .field-email { top: 429px; width: 347px; height: 32px; }
  .label-subject { top: 482px; } .field-subject { top: 500px; width: 530px; height: 32px; }
  .label-message { top: 552px; } .field-message { top: 570px; width: 530px; height: 205px; resize: none; }
  .send-button { position: absolute; left: 600px; top: 797px; width: 91px; height: 29px; border: none; border-radius: 4px;
    background: linear-gradient(180deg, var(--button-top), var(--button-bottom)); color: #ffffff;
    font-family: Georgia, "Times New Roman", serif; font-weight: 700; font-size: 14px; }

  .site-footer { position: absolute; left: 0; top: 877px; width: 1200px; height: 72px;
    background: linear-gradient(180deg, var(--footer-top) 0%, #021d38 60%, var(--footer-bottom) 100%); }
  .site-footer__note { position: absolute; left: 51px; top: 24px; font-size: 16px; color: #ffffff; }
</style>
</head>
<body>
<div class="page">
  <header class="masthead">
    <div class="masthead__band"></div>
    <div class="brand"><span class="brand__name">Brightfold Publishing</span></div>
    <nav class="main-nav">
      <a href="#" class="nav-home">Home</a>
      <a href="#" class="nav-sites">Our Sites</a>
      <a href="#" class="is-current">Contact Us</a>
    </nav>
    <h1 class="page-title">CONTACT US</h1>
    <div class="peak-art" role="img" aria-label="Illustration of a snow-capped mountain peak"></div>
  </header>

  <h2 class="section-heading details-heading">Our details</h2>
  <div class="details-card">
    <div class="details-card__company">Brightfold Publishing Pty Ltd</div>
    <div>Suite 412, 18 Carrow Lane</div>
    <div>Tamsworth Heights NSW 2041</div>
    <div class="details-card__line--gap">T: 02 9471 3086</div>
    <div class="details-card__line--gap2">E: info [at] brightfoldpublishing.com.au</div>
  </div>

  <h2 class="section-heading message-heading">Send us a message</h2>
  <form class="contact-form" action="#">
    <label class="label-name" for="contact-name">Contact Name</label>
    <input class="field field-name" id="contact-name" type="text">
    <label class="label-email" for="contact-email">Contact E-mail</label>
    <input class="field field-email" id="contact-email" type="email">
    <label class="label-subject" for="contact-subject">Subject</label>
    <input class="field field-subject" id="contact-subject" type="text">
    <label class="label-message" for="contact-message">Message</label>
    <textarea class="field field-message" id="contact-message"></textarea>
    <button class="send-button" type="submit">Send</button>
  </form>

  <footer class="site-footer">
    <p class="site-footer__note">© 2012 Brightfold Publishing</p>
  </footer>
</div>
</body>
</html>
```